Need a business card design for a residential architect.

You can get a sense of his work at www.tberlove.com

Would like a consistent look and feel between business card and website
.

Target Market(s)

Residential homeowners builders

Industry/Entity Type

Residential

Contact Information for Business Card

Dale Morrick
Principle
Morrick Architecture
418 Kestrel Lane
Alder Springs, CA 95012

dale@tberlove.com

tberlove.com
phone: 650-555-2716
Fax: 650-555-8043

Font styles to use
Sans Serif

Requirements
Must have
• Details above
Nice to have
• Would like a consistent look and feel between business card and website
Should not have
• None

```html
<!DOCTYPE html>
<html lang="en">
<head>
<meta charset="utf-8">
<title>Morrick Architecture – Business Card</title>
<link rel="stylesheet" href="https://fonts.googleapis.com/css2?family=Open+Sans:ital,wght@0,400;0,600;0,700;1,400&display=swap">
<style>
  :root {
    --backdrop: #ececec;
    --card: #f7f7f7;
    --band: #7b7b7b;
    --ink: #1e1e1e;
    --ink-soft: #3a3a3a;
    --mark: #6f6f6f;
    --on-band: #ffffff;
  }
  * { box-sizing: border-box; margin: 0; padding: 0; }
  html, body {
    width: 1200px; height: 1001px; overflow: hidden;
    background: var(--backdrop);
    font-family: "Open Sans", Arial, sans-serif;
  }
  .sheet {
    position: relative; width: 1200px; height: 1001px;
    display: flex; flex-direction: column; align-items: center; justify-content: center; gap: 60px;
  }
  .card {
    position: relative; width: 560px; height: 320px;
    background: var(--card);
    box-shadow: 0 6px 18px rgba(0,0,0,.12);
    overflow: hidden;
  }
  .band {
    position: absolute; left: 0; right: 0; bottom: 0; height: 52px;
    background: var(--band);
    display: flex; align-items: center; justify-content: center;
  }
  .band--plain { height: 26px; }
  .website { color: var(--on-band); font-weight: 700; font-size: 19px; letter-spacing: .3px; }

  .card--front .brand {
    position: absolute; left: 0; right: 0; top: 108px; text-align: center;
    color: var(--mark); font-weight: 600; font-size: 40px; letter-spacing: 1px;
  }

  .holder { position: absolute; left: 40px; top: 26px; }
  .holder__name { font-weight: 700; font-size: 19px; color: var(--ink); }
  .holder__title { font-style: italic; font-size: 13px; color: var(--ink-soft); }

  .contacts { position: absolute; left: 40px; top: 96px; list-style: none; }
  .contacts li {
    display: flex; align-items: center; gap: 10px;
    font-size: 15px; color: var(--ink-soft); line-height: 26px;
    white-space: nowrap;
  }
  .contacts svg { width: 15px; height: 15px; fill: var(--ink-soft); flex: none; }

  .card--back .brand {
    position: absolute; right: 30px; bottom: 64px;
    color: var(--mark); font-weight: 600; font-size: 24px; letter-spacing: .5px;
    line-height: 32px;
  }
</style>
</head>
<body>
<main class="sheet">

  <section class="card card--front" aria-label="Card front">
    <p class="brand">Morrick Architecture</p>
    <div class="band band--plain"></div>
  </section>

  <section class="card card--back" aria-label="Card back">
    <div class="holder">
      <p class="holder__name">Dale Morrick</p>
      <p class="holder__title">Principle</p>
    </div>
    <ul class="contacts">
      <li>
        <svg viewBox="0 0 16 16" aria-hidden="true"><path d="M2 5c0-2 2-3 6-3s6 1 6 3v1h-3V5H5v1H2zM4 7h8l2 6H2z"/></svg>
        650-555-2716
      </li>
      <li>
        <svg viewBox="0 0 16 16" aria-hidden="true"><path d="M4 1h8v4H4zM1 6h14v7h-3v2H4v-2H1zM5 10v4h6v-4z"/></svg>
        650-555-8043
      </li>
      <li>
        <svg viewBox="0 0 16 16" aria-hidden="true"><path d="M1 3h14v10H1zM2 4l6 5 6-5v-.1H2z"/></svg>
        dale@tberlove.com
      </li>
      <li>
        <svg viewBox="0 0 16 16" aria-hidden="true"><path d="M8 1a5 5 0 0 1 5 5c0 4-5 9-5 9S3 10 3 6a5 5 0 0 1 5-5zm0 3a2 2 0 1 0 0 4 2 2 0 0 0 0-4z"/></svg>
        418 Kestrel Lane Alder Springs, CA 95012
      </li>
    </ul>
    <p class="brand">Morrick Architecture</p>
    <div class="band"><span class="website">www.tberlove.com</span></div>
  </section>

</main>
</body>
</html>
```